full stationary design for a modern sleek design company

we are a design company that does modern minimalistic interior design works as well as other design services for high end clients.
we need a full stationary design including and not limited to (double sided business card, letter head, envelopes, documents folder...etc) that reflects the modern style design we do.
sleek modern and minimalistic is the requirements.
Updates

please use the latest attached files as there was a slight modification on the logo Added Wednesday, March 1, 2017

minor update on the logo files in JPG and PSD has been updated kindly follow the new attachments. Added Thursday, March 2, 2017

Target Market(s)

modern minimalist clients

Industry/Entity Type

Design Agency

Requirements
Must have
• the logo
Nice to have
• i like the colors in the colored 3D logo attached
Should not have
• too many colors

```html
<!DOCTYPE html>
<html lang="en">
<head>
<meta charset="utf-8">
<title>Forma Atelier – Business Card</title>
<link href="https://fonts.googleapis.com/css2?family=Source+Sans+3:wght@400;600&display=swap" rel="stylesheet">
<style>
  :root {
    --backdrop: #5e4d3f;
    --paper: #ffffff;
    --charcoal: #363737;
    --orange: #f7901e;
    --ink: #4a4a4a;
    --rule: #c9c9c9;
  }
  html, body {
    margin: 0;
    padding: 0;
    width: 1200px;
    height: 987px;
    overflow: hidden;
    background: var(--backdrop);
    font-family: "Source Sans 3", "Myriad Pro", Arial, sans-serif;
  }
  .stage {
    position: relative;
    width: 1200px;
    height: 987px;
  }
  .card {
    position: absolute;
    left: 293px;
    width: 615px;
    height: 350px;
    border-radius: 16px;
    overflow: hidden;
    box-shadow: 0 4px 10px rgba(0,0,0,0.35);
  }
  .card--front { top: 130px; background: var(--paper); }
  .card--back  { top: 505px; background: var(--charcoal); }

  .brand {
    position: absolute;
    display: flex;
    align-items: center;
    gap: 14px;
    font-weight: 600;
    font-size: 38px;
    letter-spacing: 4px;
    text-transform: uppercase;
    white-space: nowrap;
  }
  .brand__square {
    width: 30px;
    height: 30px;
    background: var(--orange);
    flex: none;
  }
  .card--front .brand { left: 0; right: 0; top: 84px; justify-content: center; color: var(--charcoal); }
  .card--back .brand  { left: 0; right: 0; top: 152px; justify-content: center; color: var(--orange); }
  .card--back .brand__square { background: var(--orange); }

  .person {
    position: absolute;
    right: 337px;
    top: 186px;
    text-align: right;
    color: var(--ink);
    font-size: 16px;
    line-height: 24px;
  }
  .person__name {
    color: var(--orange);
    font-weight: 600;
    font-size: 22px;
    line-height: 28px;
    letter-spacing: 0.5px;
  }
  .person__role { color: #333; }

  .divider {
    position: absolute;
    left: 302px;
    top: 190px;
    width: 1px;
    height: 96px;
    background: var(--rule);
  }

  .contacts {
    position: absolute;
    left: 317px;
    top: 190px;
    margin: 0;
    padding: 0;
    list-style: none;
    color: var(--ink);
    font-size: 16px;
  }
  .contacts li {
    display: flex;
    align-items: center;
    gap: 8px;
    height: 24px;
  }
  .contacts svg { width: 15px; height: 15px; flex: none; fill: var(--orange); }

  .footer-band {
    position: absolute;
    left: 0;
    right: 0;
    bottom: 0;
    height: 12px;
    display: flex;
  }
  .footer-band__dark { width: 305px; background: var(--charcoal); }
  .footer-band__gap { width: 3px; background: var(--paper); }
  .footer-band__accent { flex: 1; background: var(--orange); }
</style>
</head>
<body>
<main class="stage">

  <section class="card card--front" aria-label="Business card front">
    <div class="brand"><span class="brand__square"></span>Forma Atelier</div>

    <div class="person">
      <div class="person__name">MARC DELORME</div>
      <div class="person__role">CEO&amp;Founder</div>
      <div>1420 Alder Court</div>
      <div>Fairview, Oregon 97024</div>
    </div>

    <div class="divider"></div>

    <ul class="contacts">
      <li>
        <svg viewBox="0 0 16 16" aria-hidden="true"><path d="M3.6 1.2l2.4 2.6-1.4 1.9c.9 2 2.4 3.5 4.4 4.6l1.9-1.4 2.6 2.4-1.6 2.6C6.8 13.6 2.4 9.2 1.2 2.8z"/></svg>
        (555) 210 4817
      </li>
      <li>
        <svg viewBox="0 0 16 16" aria-hidden="true"><path d="M4.5 1h7a1 1 0 0 1 1 1v12a1 1 0 0 1-1 1h-7a1 1 0 0 1-1-1V2a1 1 0 0 1 1-1zm.8 2v9h5.4V3zM8 12.6a.8.8 0 1 0 0 1.6.8.8 0 0 0 0-1.6z"/></svg>
        (555) 382 6049
      </li>
      <li>
        <svg viewBox="0 0 16 16" aria-hidden="true"><path d="M1 3.5h14v9H1zm1.3 1.2L8 9l5.7-4.3z"/></svg>
        marc@formaatelier.com
      </li>
      <li>
        <svg viewBox="0 0 16 16" aria-hidden="true"><circle cx="8" cy="8" r="7"/><path d="M5 4c1.5 0 2 1 1.5 2S4 7 4.5 8.5 6 10 6 12M10 3c-.5 1.5.5 2.5 2 2.5M11 10c-1 0-2 .8-1.5 2.5" stroke="#fff" stroke-width="1.1" fill="none"/></svg>
        www.formaatelier.com
      </li>
    </ul>

    <div class="footer-band">
      <div class="footer-band__dark"></div>
      <div class="footer-band__gap"></div>
      <div class="footer-band__accent"></div>
    </div>
  </section>

  <section class="card card--back" aria-label="Business card back">
    <div class="brand"><span class="brand__square"></span>Forma Atelier</div>
  </section>

</main>
</body>
</html>
```